Brand and Marketing Coach Needs PDF Designed

I have content that i need placed into a simple but great PDF design. The PDF is about the formula I use to build personal brands. This is geared towards entrepreneurs, experts, coaches, therapists, wellness practitioners, and indpendent business owners who serve to improve the lives of others.
The company name is changing from TorvelCast to Selling with the Village (I don't have that logo yet, so working backwards a bit. For now, the TorvelCast logo can be used.) My brand is NOT formal and corporate, but it's also not neon-pink and screaming at you. It's down to earth, hip, a bit modern but warm. It's about no BS and authenticity. The final deliverable should make the reader feel focused, smart, motivated and hopeful.

Target Market(s)

Conscious entrepreneurs and small business owners. this one is specifically for pharmacy entrepreneurs but this will be used for various audiences later.

Font styles to use
Sans Serif

Colors
eaf1f7
3377b5
6b449b
f37122
faa54b
f68e4e
ffc214

Requirements
Must have
• Modern design. colors that match logo - 4e5583 (i think that is the blue.) d65a40.
• Could have these colors as well: c6a254, 01bcc3
• But open to other colors
Nice to have
• I'd like to see some ways to make this PDF simple and readable, and eye-catching. I'd also like to use the uploaded ebooks for design ideas.
Should not have
• neon colors, clip art

```html
<!DOCTYPE html>
<html lang="en">
<head>
<meta charset="utf-8">
<title>Follow the Personal Brand Formula</title>
<link href="https://fonts.googleapis.com/css2?family=Playfair+Display:wght@400;700&family=Lato:ital,wght@0,400;0,700;1,400&display=swap" rel="stylesheet">
<style>
  :root {
    --canvas: #ffffff;
    --page: #ffffff;
    --page-edge: #e2e2e6;
    --brand-blue: #4e5583;
    --accent-orange: #f37122;
    --heading-ink: #3d3f52;
    --body-ink: #6d6f7a;
    --white: #ffffff;
  }
  * { box-sizing: border-box; margin: 0; padding: 0; }
  html, body { width: 795px; height: 1200px; overflow: hidden; background: var(--canvas); }
  .spread {
    position: relative;
    width: 795px;
    height: 1200px;
    display: grid;
    grid-template-columns: 388px 388px;
    grid-template-rows: repeat(4, 290px);
    column-gap: 9px;
    row-gap: 10px;
    padding: 5px;
  }
  .page {
    background: var(--page);
    border: 1px solid var(--page-edge);
    box-shadow: 0 1px 3px rgba(0,0,0,0.08);
    padding: 24px 26px 18px;
    display: flex;
    flex-direction: column;
    gap: 14px;
    overflow: hidden;
  }
  .page--feature {
    background: var(--brand-blue);
    border-color: var(--brand-blue);
    color: var(--white);
    font-family: "Playfair Display", serif;
  }
  .cover { align-items: center; text-align: center; padding-top: 40px; gap: 4px; }
  .cover__number { font-size: 70px; line-height: 1; font-weight: 400; }
  .cover__title { font-size: 27px; line-height: 1.12; font-weight: 400; letter-spacing: 1.5px; text-transform: uppercase; }
  .next { justify-content: flex-end; padding-bottom: 34px; padding-left: 30px; }
  .next__title { font-size: 32px; line-height: 1.1; font-weight: 400; letter-spacing: 1.5px; text-transform: uppercase; }

  .step { flex: 1; display: flex; flex-direction: column; gap: 5px; }
  .step__head { display: flex; align-items: baseline; gap: 8px; }
  .step__number { font-family: "Playfair Display", serif; color: var(--accent-orange); font-size: 20px; line-height: 1; }
  .step__name { font-family: "Playfair Display", serif; color: var(--accent-orange); font-size: 12px; font-weight: 700; letter-spacing: 1px; text-transform: uppercase; }
  .step__lead { font-family: "Lato", sans-serif; font-weight: 700; color: var(--heading-ink); font-size: 7.5px; line-height: 1.4; }
  .step__body { font-family: "Lato", sans-serif; color: var(--body-ink); font-size: 6.5px; line-height: 1.6; }
  .step__note { font-family: "Lato", sans-serif; font-style: italic; color: var(--heading-ink); font-size: 6.5px; }

  .iceberg { gap: 10px; padding-top: 30px; }
  .iceberg__title { font-family: "Playfair Display", serif; color: var(--heading-ink); font-size: 11px; font-weight: 700; }
  .iceberg__list { list-style: none; display: flex; flex-direction: column; gap: 8px; font-family: "Lato", sans-serif; color: var(--body-ink); font-size: 6.5px; line-height: 1.6; }
</style>
</head>
<body>
<main class="spread">

  <section class="page page--feature cover">
    <div class="cover__number">3</div>
    <h1 class="cover__title">Follow the<br>Personal<br>Brand Formula</h1>
  </section>

  <section class="page">
    <article class="step">
      <div class="step__head"><span class="step__number">1</span><h2 class="step__name">Motivators</h2></div>
      <p class="step__lead">Your WHY and the real reasons you started this business.</p>
      <p class="step__body">Every brand begins with a purpose. Name what moves you to serve, what keeps you going on hard days, and the change you want to see in the lives of the people you help. Write it down in plain words and keep it close. This is the fuel behind every message you share, every offer you create and every client you welcome, and it reminds you why the work matters.</p>
    </article>
    <article class="step">
      <div class="step__head"><span class="step__number">2</span><h2 class="step__name">Value</h2></div>
      <p class="step__lead">Your expertise and the results your clients get from working with you.</p>
      <p class="step__body">List the skills, training and lived experience you bring. Then describe the outcomes people enjoy after working with you, in words they would use themselves. Focus on the change, not the method: more time, more calm, more confidence, better health. When your value is clear, the right people see it at once and know you are the one to call.</p>
    </article>
  </section>

  <section class="page">
    <article class="step">
      <div class="step__head"><span class="step__number">3</span><h2 class="step__name">Your Ideal Client</h2></div>
      <p class="step__lead">The client for whom you absolutely know you can serve at the highest level.</p>
      <p class="step__body">Picture one person you love to help. Know their daily struggles, their hopes and the words they use when they ask for help. Learn where they spend time, what they read and who they trust. When you speak to one person clearly, many more who share those needs will feel that you understand them.</p>
    </article>
    <article class="step">
      <div class="step__head"><span class="step__number">4</span><h2 class="step__name">Positioning / Representation</h2></div>
      <p class="step__lead">The strategy you use to establish yourself as the expert.</p>
      <p class="step__body">Choose where you show up and how you want to be seen. Own a clear place in your market so the right people find you first. Share useful ideas, speak at local events and build steady proof of your skill.</p>
      <p class="step__note">Remaining true to your values builds lasting trust.</p>
    </article>
  </section>

  <section class="page">
    <article class="step">
      <div class="step__head"><span class="step__number">5</span><h2 class="step__name">Your Story</h2></div>
      <p class="step__lead">The relatable circumstances that brought you to create this business.</p>
      <p class="step__body">Share the turning points, the doubts and the wins along the way. A true story lets people see themselves in your journey. Keep it honest and simple, and connect each chapter to the reason you now serve the people you do.</p>
    </article>
    <article class="step">
      <div class="step__head"><span class="step__number">6</span><h2 class="step__name">Personality - Your Character</h2></div>
      <p class="step__lead">Of course you have a personality, but this is all about how you relay that.</p>
      <p class="step__body">Let your humor, warmth and quirks come through. People buy from people, so show the human behind the brand in every post and page. Pick a few traits you want others to notice and let them guide your words, your colors and the way you greet each new client.</p>
    </article>
  </section>

  <section class="page">
    <article class="step">
      <div class="step__head"><span class="step__number">7</span><h2 class="step__name">Communication Style</h2></div>
      <p class="step__lead">The way you speak and how you engage with your audience.</p>
      <p class="step__body">Pick a tone and keep it steady across email, video and social posts. Speak plainly, listen well and answer questions the way a good friend would. Reply to comments, ask for feedback and turn one-way posts into real conversations with the people you serve.</p>
    </article>
    <article class="step">
      <div class="step__head"><span class="step__number">8</span><h2 class="step__name">Authenticity - Transparency</h2></div>
      <p class="step__lead">Being human. Being real. Being transparent.</p>
      <p class="step__body">Show what is working and what is not. Admit mistakes, share the process and let your audience see the real you behind the results. Be open about prices, timelines and what clients can expect, so nobody is ever surprised along the way.</p>
    </article>
  </section>

  <section class="page">
    <article class="step">
      <div class="step__head"><span class="step__number">9</span><h2 class="step__name">Trust</h2></div>
      <p class="step__lead">People buy from and do business with people they trust, for reasons that are easy to see.</p>
      <p class="step__body">Keep your promises, deliver on time and be consistent. Trust grows slowly through small proof points, honest reviews and steady results. Show up the same way each week, follow through on what you say and thank the people who spread the word.</p>
      <p class="step__body">When every step of the formula works together, trust becomes the natural result and your brand starts to grow on its own.</p>
    </article>
    <div class="step"></div>
  </section>

  <section class="page page--feature next">
    <h2 class="next__title">What's<br>Next?</h2>
  </section>

  <section class="page iceberg">
    <h2 class="iceberg__title">This is just the tip of the iceberg.</h2>
    <ol class="iceberg__list">
      <li>1. Use the formula to map out your brand one step at a time. Work through each part, write your answers and review them every few months as your business grows.</li>
      <li>2. Book a free strategy call to talk through your next move with our team. We will help you find the gaps and choose the steps that matter most right now.</li>
      <li>3. Join our community for weekly tips, fresh ideas and support from other business owners who are building brands of their own.</li>
    </ol>
  </section>

</main>
</body>
</html>
```